Brindle Water - 500ml

to create a water bottle packaging similar to L'onde Claire design. Bottle should be blue similar to PURE FLOW but change the design/logo to Brindle. Wording should be similar just different design and logo. Thanks.

Colors
0054AA
0677BA
7BADD7
CADEEF
E8F1F8

Requirements
Must have
• Bottle must not be in plastic bottles. They are made in a carton instead - see PURE FLOW for reference.

```html
<!DOCTYPE html>
<html lang="en">
<head>
<meta charset="utf-8">
<title>Brindle Water – 500 ml carton</title>
<link rel="stylesheet" href="https://fonts.googleapis.com/css2?family=Oswald:wght@500;600&family=Open+Sans:wght@400;700&display=swap">
<style>
  :root {
    --backdrop: #8a8c90;
    --carton-navy: #122b5e;
    --pattern-blue: #0b4f9a;
    --band-blue: #1c62b3;
    --ink-white: #ffffff;
    --ink-pale: #cadeef;
    --ink-mist: #e8f1f8;
  }
  * { box-sizing: border-box; margin: 0; padding: 0; }
  html, body {
    width: 843px; height: 1200px; overflow: hidden;
    background: var(--backdrop);
  }
  .canvas {
    position: relative; width: 843px; height: 1200px;
  }
  .carton-front {
    position: absolute; left: 201px; top: 90px;
    width: 440px; height: 1060px;
    background: var(--carton-navy);
    overflow: hidden;
  }
  .brand {
    position: absolute; top: 80px; left: 0; width: 100%;
    text-align: center; color: var(--ink-white);
  }
  .brand-name {
    font-family: "Oswald", sans-serif; font-weight: 600;
    font-size: 64px; line-height: 1; letter-spacing: 1px;
  }
  .brand-tagline {
    margin-top: 8px;
    font-family: "Open Sans", sans-serif; font-size: 9px;
    letter-spacing: 1.5px; color: var(--ink-pale);
  }
  .pattern-band {
    position: absolute; left: 0; width: 100%;
    background: var(--pattern-blue);
  }
  .pattern-band.top { top: 295px; height: 130px; }
  .pattern-band.bottom { top: 695px; height: 125px; }
  .product-band {
    position: absolute; left: 0; top: 425px; width: 100%; height: 270px;
    background: var(--band-blue);
    display: flex; align-items: center; justify-content: center;
  }
  .product-name {
    font-family: "Oswald", sans-serif; font-weight: 500;
    font-size: 118px; letter-spacing: 2px; color: var(--ink-white);
  }
  .details {
    position: absolute; top: 865px; left: 0; width: 100%;
    text-align: center; font-family: "Open Sans", sans-serif;
  }
  .details-headline {
    font-weight: 700; font-size: 27px; color: var(--ink-white);
  }
  .details-copy {
    margin-top: 6px; font-size: 19px; line-height: 1.3; color: var(--ink-mist);
  }
  .volume {
    position: absolute; top: 1055px; left: 0; width: 100%;
    text-align: center; font-family: "Oswald", sans-serif; font-weight: 500;
    font-size: 32px; color: var(--ink-white);
  }
</style>
</head>
<body>
<main class="canvas">
  <section class="carton-front">
    <header class="brand">
      <div class="brand-name">Brindle</div>
      <div class="brand-tagline">PURE SPRING WATER SINCE 1898</div>
    </header>

    <div class="pattern-band top" role="img" aria-label="Band of repeating blue ocean wave scrolls"></div>
    <div class="product-band">
      <h1 class="product-name">WATER</h1>
    </div>
    <div class="pattern-band bottom" role="img" aria-label="Band of repeating blue ocean wave scrolls"></div>

    <div class="details">
      <p class="details-headline">100% Spring Water</p>
      <p class="details-copy">Sustainably sourced water<br>in a plant-based carton</p>
    </div>
    <p class="volume">500 ML</p>
  </section>
</main>
</body>
</html>
```